project - Misto Den

Dear designers, I'm Looking for an appealing new business card design to represent us for our new e-cigarette store: The MistO Den. Knowledgeable and friendly staff we aim for superior customer service with a positive atmosphere. Classic feel with modern touch is what we are aiming for . Lime green font and grey back round is the original color scheme but we are flexible and open to suggestions. I added some doodles to show you where my mind is at. address: 4827 203 St SW Edmonton, AB (inside the grand swap bazaar)web: themistoden.com email: info@themistoden.com phone : 555.214.6093 Thanks and am looking forward to seeing your creative , fresh and innovative designs.
Good luck everybody!
Gordon
Updates
lime green and charcoal grey please. thanks
Industry/Entity Type
Business
Logo Text
The MistO Den
Look and feel
Each slider illustrates characteristics of the customer's brand and the style your logo design should communicate.

```html
<!DOCTYPE html>
<html lang="en">
<head>
<meta charset="utf-8">
<title>The MistO Den — Business Card</title>
<link rel="stylesheet" href="https://fonts.googleapis.com/css2?family=Cabin:wght@400;500&display=swap">
<style>
  :root {
    --page: #ffffff;
    --charcoal: #252b2d;
    --smoke: #3a4244;
    --lime: #b8f01c;
    --grey: #8a8c8c;
    --rule-grey: #9a9c9c;
  }
  * { margin: 0; padding: 0; box-sizing: border-box; }
  html, body {
    width: 1200px; height: 1000px; overflow: hidden;
    background: var(--page);
    font-family: "Cabin", "Trebuchet MS", sans-serif;
  }
  .card {
    position: absolute; left: 57px; top: 181px;
    width: 1086px; height: 637px;
    background: var(--charcoal);
    overflow: hidden;
  }
  .smoke-decoration {
    position: absolute; left: 860px; top: 0;
    width: 226px; height: 637px;
    background: radial-gradient(ellipse at 60% 60%, var(--smoke) 0%, rgba(58,66,68,0.45) 40%, rgba(37,43,45,0) 75%);
  }
  .brand { position: absolute; left: 93px; top: 395px; }
  .brand-name {
    display: flex; align-items: center; gap: 12px;
    color: var(--lime); font-size: 48px; font-weight: 500;
    letter-spacing: -1px; line-height: 1;
  }
  .brand-dot {
    width: 16px; height: 16px; border-radius: 50%;
    background: var(--lime);
  }
  .brand-tagline {
    margin: 8px 0 0 88px;
    color: var(--grey); font-size: 28px; font-weight: 400; line-height: 1;
  }
  .address {
    position: absolute; left: 66px; top: 503px;
    color: var(--lime); font-size: 27px; font-weight: 500; line-height: 34px;
  }
  .rule { position: absolute; width: 3px; }
  .rule-lime { left: 571px; top: 396px; height: 194px; background: var(--lime); }
  .rule-grey { left: 577px; top: 382px; height: 194px; background: var(--rule-grey); }
  .contacts {
    position: absolute; left: 652px; top: 462px;
    list-style: none;
  }
  .contacts li {
    display: flex; align-items: center; gap: 8px;
    color: var(--lime); font-size: 27px; font-weight: 500;
    height: 40px;
  }
  .contacts svg { width: 36px; height: 30px; flex: none; }
</style>
</head>
<body>
  <main class="card">
    <div class="smoke-decoration" role="img" aria-label="Faint rising smoke swirl decoration"></div>

    <div class="brand">
      <div class="brand-name"><span>The MistO Den</span><span class="brand-dot"></span></div>
      <div class="brand-tagline">e-cigarette store</div>
    </div>

    <p class="address">4827 203 St SW Edmonton<br>AB (inside the grand swap bazaar)</p>

    <span class="rule rule-grey"></span>
    <span class="rule rule-lime"></span>

    <ul class="contacts">
      <li>
        <svg viewBox="0 0 36 30" aria-hidden="true">
          <g fill="none" stroke="#8a8c8c" stroke-width="1.5">
            <circle cx="18" cy="15" r="13"/>
            <ellipse cx="18" cy="15" rx="6" ry="13"/>
            <line x1="5" y1="15" x2="31" y2="15"/>
            <line x1="7" y1="8" x2="29" y2="8"/>
            <line x1="7" y1="22" x2="29" y2="22"/>
          </g>
        </svg>
        <span>: themistoden.com</span>
      </li>
      <li>
        <svg viewBox="0 0 36 30" aria-hidden="true">
          <g fill="none" stroke="#8a8c8c" stroke-width="1.8">
            <rect x="3" y="7" width="30" height="17"/>
            <polyline points="3,7 18,18 33,7"/>
          </g>
        </svg>
        <span>: info@themistoden.com</span>
      </li>
      <li>
        <svg viewBox="0 0 36 30" aria-hidden="true">
          <path fill="#8a8c8c" d="M12 3c-2 0-4 2-4 5 0 8 7 17 15 19 3 1 5-1 5-3l-4-4-3 2c-3-2-6-6-7-10l2-3z"/>
        </svg>
        <span>: 555.214.6093</span>
      </li>
    </ul>
  </main>
</body>
</html>
```